Refresh Brightpath Coursecraft

Need a new design for e-learning development and web app development site: http://brightpathcoursecraft.example. Need pages for everything on menu bar plus a training services and a web app development services pages and a better page for samples http://brightpathcoursecraft.example/samples5/.

***Must be programmed in html 5. NO CMS. No WP. No Plume. Straight html/css.

Target Market(s)

government

Industry/Entity Type

Government

Coding

Coded - Design and coding required

Number of Pages Required

1 page

Requirements
Must have
• Must be coded in html5/css. No CMS.
• Divided so you can easily see that we offer 3 separate services:
• Live Training - E-Learning Development - Web App Development
• A way to display logos of all our clients like on bottom of this page: https://www.quorvatests.example (this is also our website so you can copy all these logos)
• List both our Denver location which is already on our website plus our office in Velmoro Plaza. Street 62 Sur, 14-87. Medellín, Antioquia.
• A page like this for our web app dev services https://www.tekvanu.example/product-development
Should not have
• CMS

```html
<!DOCTYPE html>
<html lang="en">
<head>
<meta charset="utf-8">
<title>Brightpath Coursecraft</title>
<link rel="stylesheet" href="https://fonts.googleapis.com/css2?family=Montserrat:wght@500;700;800;900&family=Open+Sans:wght@400;600;700&display=swap">
<style>
:root{
  --blue:#1f78b9;
  --blue-dark:#1a5f95;
  --blue-deep:#155a8c;
  --orange:#f07b22;
  --ink:#141414;
  --text:#6d6d6d;
  --grey:#f1f1f1;
  --white:#ffffff;
}
*{box-sizing:border-box;margin:0;padding:0}
html,body{width:1200px;height:4196px;overflow:hidden}
body{position:relative;background:var(--white);font-family:'Open Sans',sans-serif;color:var(--text)}
.abs{position:absolute}
.btn{position:absolute;display:inline-block;background:var(--orange);color:var(--white);font:700 12px 'Montserrat',sans-serif;letter-spacing:.5px;padding:12px 22px;box-shadow:0 4px 8px rgba(0,0,0,.15)}
.rule{position:absolute;width:64px;height:3px;display:flex}
.rule span{flex:1;background:var(--orange)}
.rule span:last-child{background:var(--blue)}
.section-title{position:absolute;left:0;width:1200px;text-align:center;font:900 38px 'Montserrat',sans-serif;color:var(--ink)}
/* header */
.site-header{position:absolute;top:0;left:0;width:1200px;height:94px;background:var(--white);box-shadow:0 2px 6px rgba(0,0,0,.06);z-index:3}
.brand{position:absolute;left:110px;top:22px;display:flex;align-items:center;gap:10px}
.brand-mark{width:44px;height:44px;border-radius:50%;background:var(--blue)}
.brand-name{font:700 20px 'Montserrat',sans-serif;color:var(--blue);line-height:1.05}
.brand-sub{font:500 10px 'Montserrat',sans-serif}
.nav{position:absolute;right:110px;top:38px;display:flex;gap:30px;font:500 13px 'Montserrat',sans-serif;color:#222}
/* hero */
.hero{position:absolute;top:94px;left:0;width:1200px;height:640px}
.hero h1{position:absolute;left:135px;top:150px;z-index:2;white-space:nowrap;font:900 37px/1.22 'Montserrat',sans-serif;color:var(--ink)}
.hero h1 em{font-style:normal;color:var(--blue)}
.hero-art{position:absolute;left:655px;top:20px;width:440px;height:430px;border-radius:20px;background:radial-gradient(circle at 50% 55%,#e6e9f4,#f6f7fb 70%)}
.arrows{position:absolute;display:flex;gap:16px;font:700 20px 'Montserrat',sans-serif;color:#111}
/* intro */
.intro h2{position:absolute;left:0;width:1200px;top:745px;text-align:center;font:900 38px/1.18 'Montserrat',sans-serif;color:var(--ink)}
.intro p{position:absolute;left:128px;width:944px;text-align:center;font:400 12.5px/1.75 'Open Sans',sans-serif;color:#333}
/* services */
.service h3{position:absolute;font:900 28px 'Montserrat',sans-serif;color:var(--ink)}
.service p{position:absolute;width:430px;font:400 15px/1.75 'Open Sans',sans-serif;color:var(--text)}
.service-art{position:absolute;border-radius:14px}
.band-grey{position:absolute;left:0;width:1200px;background:var(--grey)}
/* clients */
.clients-grid{position:absolute;left:115px;top:2865px;display:grid;grid-template-columns:repeat(4,225px);gap:24px 24px}
.client{height:178px;background:var(--white);box-shadow:0 3px 14px rgba(0,0,0,.12);display:flex;flex-direction:column;align-items:center;justify-content:center;gap:12px}
.client-dot{width:34px;height:34px;border-radius:50%;background:var(--blue-dark)}
.client-name{font:700 15px 'Montserrat',sans-serif;color:#2a3a5c;text-align:center;padding:0 10px}
/* contact */
.cta-title{position:absolute;left:0;width:1200px;top:3538px;text-align:center;font:800 25px 'Montserrat',sans-serif;color:var(--ink)}
.cta-phone{position:absolute;left:0;width:1200px;top:3570px;text-align:center;font:800 53px 'Montserrat',sans-serif;color:var(--blue)}
/* footer */
.site-footer{position:absolute;left:0;top:3745px;width:1200px;height:390px;background:var(--blue)}
.footer-brand{position:absolute;left:115px;top:40px;display:flex;align-items:center;gap:10px}
.footer-brand .brand-mark{background:var(--white)}
.footer-brand .brand-name{color:var(--white)}
.footer-links{position:absolute;left:120px;top:120px;list-style:none;font:400 13px 'Open Sans',sans-serif;color:var(--white)}
.footer-links li{height:31px;display:flex;align-items:center;gap:20px}
.footer-links li::before{content:"";width:0;height:0;border-left:5px solid var(--white);border-top:4px solid transparent;border-bottom:4px solid transparent}
.footer-contact{position:absolute;left:385px;top:50px;width:275px;color:var(--white)}
.footer-contact h4{font:800 24px 'Montserrat',sans-serif;margin-bottom:22px}
.c-row{display:flex;gap:16px;font:400 12px/2 'Open Sans',sans-serif;margin-bottom:2px}
.c-row svg{flex:none;margin-top:6px}
.c-row span{min-width:0;overflow-wrap:anywhere}
.c-row b{font-weight:700}
.map{position:absolute;left:677px;top:50px;width:410px;height:275px;background:linear-gradient(135deg,#e7ecea,#d6dedb);border:2px solid var(--white)}
.footer-bar{position:absolute;left:0;top:4135px;width:1200px;height:61px;background:var(--blue-deep);color:var(--white);font:400 12px 'Open Sans',sans-serif}
.footer-bar .copy{position:absolute;left:0;width:1200px;top:22px;text-align:center}
</style>
</head>
<body>

<header class="site-header">
  <div class="brand"><span class="brand-mark"></span><span class="brand-name">Brightpath<br><span class="brand-sub">COURSECRAFT</span></span></div>
  <nav class="nav"><span>HOME</span><span>SERVICES</span><span>PORTFOLIO</span><span>TEAM &amp; EXPERIENCE</span><span>CONTACTS</span></nav>
</header>

<section class="hero">
  <svg class="abs" style="left:0;top:0" width="1200" height="640" viewBox="0 0 1200 640" aria-hidden="true">
    <rect width="1200" height="640" fill="#f1f1f1"/>
    <path d="M0 0H1200V410Q600 800 0 410Z" fill="#ffffff"/>
    <path d="M0 410Q600 800 1200 410L1200 440Q600 850 0 440Z" fill="#1f78b9"/>
  </svg>
  <div class="hero-art" role="img" aria-label="Illustration of a person working at a desk surrounded by books and learning objects"></div>
  <h1>WE CREATE <em>ENGAGING<br>TRAINING</em> THAT EXCEED<br>EXPECTATIONS.</h1>
  <a class="btn" style="left:143px;top:313px">READ MORE</a>
  <div class="arrows" style="left:581px;top:512px"><span>‹</span><span>›</span></div>
</section>

<section class="intro">
  <h2>INSTRUCTIONAL DESIGN AND<br>COURSEWARE DEVELOPMENT FIRM</h2>
  <div class="rule" style="left:568px;top:852px"><span></span><span></span></div>
  <p style="top:872px">Brightpath Coursecraft is a HUBZone Certified, SBA 8(a) Certified, Native American Owned Small Disadvantaged Business located in Denver, Colorado. We have designed and delivered SCORM compliant eLearning, webinar, web-based training (WBT), instructor-led training (ILT), virtual ILT (vILT), blended, and 3D immersive training courses. The Instructional Design Team brings nearly one hundred years of Instructional Design experience.</p>
  <p style="top:962px">Our Instructional Designers have experience designing, developing, and delivering custom technical and business skill training courses. This encompasses a variety of industries, including pharmaceuticals, financial, real estate/property management, health care, telecommunications, financial, government, oil and gas, software/technology, manufacturing, Higher Ed, and K-12.</p>
  <a class="btn" style="left:538px;top:1059px">READ MORE</a>
</section>

<svg class="abs" style="left:0;top:1120px" width="1200" height="110" aria-hidden="true"><polygon points="0,0 1200,100 1200,110 0,110" fill="#ffffff"/><polygon points="0,0 1200,100 1200,0" fill="#f1f1f1"/></svg>

<h2 class="section-title" style="top:1235px">OUR SERVICES</h2>
<div class="rule" style="left:568px;top:1292px"><span></span><span></span></div>

<section class="service">
  <h3 style="left:122px;top:1390px">LIVE TRAINING</h3>
  <p style="left:122px;top:1440px">Sed ut perspiciatis unde omnis iste natus error sit voluptatem accusantium doloremque laudantium, totam rem aperiam, eaque ipsa quae ab illo inventore veritatis et quasi architecto beatae vitae dicta sunt explicabo. Nemo enim ipsam voluptatem quia voluptas sit aspernatur aut odit aut fugit,</p>
  <a class="btn" style="left:122px;top:1593px">READ MORE</a>
  <div class="service-art" style="left:655px;top:1355px;width:375px;height:320px;background:radial-gradient(circle,#dfe9f5,#fafafa 72%)" role="img" aria-label="Illustration of a monitor showing a live video lesson with gears and books"></div>
</section>

<div class="band-grey" style="top:1720px;height:405px"></div>
<section class="service">
  <div class="service-art" style="left:125px;top:1800px;width:460px;height:240px;background:radial-gradient(circle,#e4ebe2,#f1f1f1 72%)" role="img" aria-label="Illustration of a laptop displaying video course modules beside a coffee cup and books"></div>
  <h3 style="left:650px;top:1805px">E-LEARNING DEVELOPMENT</h3>
  <p style="left:650px;top:1860px">Sed ut perspiciatis unde omnis iste natus error sit voluptatem accusantium doloremque laudantium, totam rem aperiam, eaque ipsa quae ab illo inventore veritatis et quasi architecto beatae vitae dicta sunt explicabo. Nemo enim ipsam voluptatem quia voluptas sit aspernatur aut odit aut fugit,</p>
  <a class="btn" style="left:650px;top:2015px">READ MORE</a>
</section>

<section class="service">
  <h3 style="left:122px;top:2268px">WEB APP DEVELOPMENT</h3>
  <p style="left:122px;top:2315px">Sed ut perspiciatis unde omnis iste natus error sit voluptatem accusantium doloremque laudantium, totam rem aperiam, eaque ipsa quae ab illo inventore veritatis et quasi architecto beatae vitae dicta sunt explicabo. Nemo enim ipsam voluptatem quia voluptas sit aspernatur aut odit aut fugit,</p>
  <a class="btn" style="left:122px;top:2468px">READ MORE</a>
  <div class="service-art" style="left:605px;top:2180px;width:465px;height:410px;background:radial-gradient(circle,#dce9f6,#ffffff 72%)" role="img" aria-label="Illustration of a team building a web dashboard on a large screen"></div>
</section>

<svg class="abs" style="left:0;top:2630px" width="1200" height="1115" aria-hidden="true">
  <polygon points="0,0 1200,75 1200,1115 0,1115" fill="#f1f1f1"/>
  <polygon points="0,770 1200,870 1200,1115 0,1115" fill="#ffffff"/>
</svg>

<h2 class="section-title" style="top:2765px">OUR CLIENTS</h2>
<div class="rule" style="left:568px;top:2822px"><span></span><span></span></div>
<div class="clients-grid">
  <div class="client"><span class="client-dot"></span><span class="client-name">Workreach Corps</span></div>
  <div class="client"><span class="client-dot"></span><span class="client-name">Harlow County</span></div>
  <div class="client"><span class="client-dot"></span><span class="client-name">Ridgecrest University</span></div>
  <div class="client"><span class="client-dot"></span><span class="client-name">Skyward Command</span></div>
  <div class="client"><span class="client-dot"></span><span class="client-name">Delmont Institute</span></div>
  <div class="client"><span class="client-dot"></span><span class="client-name">Verdanta</span></div>
  <div class="client"><span class="client-dot"></span><span class="client-name">Clarivex</span></div>
  <div class="client"><span class="client-dot"></span><span class="client-name">Ashford &amp; Lyle College</span></div>
</div>
<div class="arrows" style="left:581px;top:3330px"><span>‹</span><span>›</span></div>

<section class="cta">
  <h2 class="cta-title">CONTACT US TODAY FOR A FREE CONSULTATION</h2>
  <p class="cta-phone">888-555-0147 X210</p>
</section>

<footer class="site-footer">
  <div class="footer-brand"><span class="brand-mark"></span><span class="brand-name">Brightpath<br><span class="brand-sub">COURSECRAFT</span></span></div>
  <ul class="footer-links">
    <li>Home</li><li>About Us</li><li>Services</li><li>Portfolio</li><li>Team &amp; Experience</li><li>Contact Us</li>
  </ul>
  <div class="footer-contact">
    <h4>CONTACTS</h4>
    <div class="c-row"><svg width="12" height="16" viewBox="0 0 12 16"><path d="M6 0a6 6 0 0 1 6 6c0 4-6 10-6 10S0 10 0 6a6 6 0 0 1 6-6z" fill="#fff"/><circle cx="6" cy="6" r="2.2" fill="#1f78b9"/></svg><span>5820 E Larkspur Avenue, Suite 2-140<br>Aurora, CO 80019</span></div>
    <div class="c-row"><svg width="14" height="14" viewBox="0 0 14 14"><path d="M3 0l3 3-2 2c1 2 3 4 5 5l2-2 3 3-2 3C6 14 0 8 0 2z" fill="#fff"/></svg><span>Telephone: +1 888 555 0147</span></div>
    <div class="c-row"><svg width="14" height="11" viewBox="0 0 14 11"><rect width="14" height="11" fill="#fff"/><path d="M0 0l7 6 7-6" stroke="#1f78b9" fill="none"/></svg><span>E-mail:<br>support@brightpathcoursecraft.example</span></div>
    <div class="c-row" style="margin-top:16px"><svg width="12" height="16" viewBox="0 0 12 16"><path d="M6 0a6 6 0 0 1 6 6c0 4-6 10-6 10S0 10 0 6a6 6 0 0 1 6-6z" fill="#fff"/><circle cx="6" cy="6" r="2.2" fill="#1f78b9"/></svg><span><b>Another Address :</b><br>Velmoro Plaza. Street 62 Sur, 14-87<br>Medellín, Antioquia</span></div>
  </div>
  <div class="map" role="img" aria-label="Map showing the office location"></div>
</footer>
<div class="footer-bar"><span class="copy">© 2019 &nbsp;|&nbsp; www.brightpathcoursecraft.example</span></div>

</body>
</html>
```